Business card and (possibly) logo

Hi - we need a new business card.
We have an existing logo that we quite like but we are open to options.
We are an architectural firm - we specialize in upmarket residential work and apartment blocks.
We are chasing a business card at present but also want to extensively update our website going forward to attract a much higher level of client / investor / developer.
Our current logo is black, grey and yellow and based on the sun/moon temples in Mexico.
We are open to variations.
We want to communicate professionalism, trust, quality.
Our website is www.halvorenarchitects.com.au - but note as above - we want to change the website as well to be a lot 'classier' and to appeal to a higher end market.

thanks

Target Market(s)

We are an architect firm - our target market is Developers and builders of high end houses and luxury apartment blocks. Also private home owners wanting to build excellent expensive houses. (ideally over $1m budgets)

Industry/Entity Type

Residential

Requirements
Must have
• Logo
Contact details;
Name
phone, mobile, email, web

```html
<!DOCTYPE html>
<html lang="en">
<head>
<meta charset="utf-8">
<title>Halvoren Architects — Business Card</title>
<link rel="stylesheet" href="https://fonts.googleapis.com/css2?family=Open+Sans:wght@400;700&family=Ubuntu:wght@400;500&display=swap">
<style>
  :root {
    --card-bg: #ffffff;
    --accent: #f5a01a;
    --text-grey: #6b6b6b;
    --contact-grey: #4f4f4f;
    --icon-grey: #7a7a7a;
    --rule-grey: #9a9a9a;
    --brand-grey: #8a8a8a;
    --band: #000000;
    --emblem-light: #f2f2f2;
    --emblem-sun: #fbe3b8;
  }
  html, body {
    margin: 0;
    padding: 0;
    width: 1200px;
    height: 734px;
    overflow: hidden;
    background: var(--card-bg);
  }
  .card {
    position: relative;
    width: 1200px;
    height: 734px;
    background: var(--card-bg);
    overflow: hidden;
  }
  .emblem {
    position: absolute;
    z-index: 0;
    left: 0;
    top: 340px;
    width: 420px;
    height: 354px;
    background: radial-gradient(ellipse at 22% 22%, var(--emblem-sun) 0%, rgba(251,227,184,0.4) 20%, var(--emblem-light) 48%, rgba(242,242,242,0) 100%);
  }
  .person {
    position: absolute;
    z-index: 1;
    right: 872px;
    top: 110px;
    text-align: right;
    font-family: "Open Sans", sans-serif;
  }
  .person__name {
    margin: 0;
    font-size: 34px;
    font-weight: 700;
    color: var(--accent);
    line-height: 1.2;
  }
  .person__role {
    margin: 6px 0 0;
    font-size: 34px;
    font-weight: 400;
    color: var(--text-grey);
    line-height: 1.2;
  }
  .contacts {
    position: absolute;
    z-index: 1;
    left: 428px;
    top: 92px;
    margin: 0;
    padding: 0;
    list-style: none;
    font-family: "Ubuntu", sans-serif;
    font-size: 31px;
    color: var(--contact-grey);
  }
  .contacts__item {
    display: flex;
    align-items: flex-start;
    height: 48px;
    line-height: 44px;
  }
  .contacts__item--gap { margin-top: 32px; }
  .contacts__item--tall { height: auto; margin-top: 6px; }
  .contacts__icon {
    width: 40px;
    height: 44px;
    flex: none;
  }
  .contacts__icon svg {
    width: 36px;
    height: 36px;
    margin-top: 4px;
    fill: none;
    stroke: var(--icon-grey);
    stroke-width: 2.4;
  }
  .contacts__rule {
    width: 2px;
    height: 26px;
    margin: 10px 14px 0 14px;
    background: var(--rule-grey);
    flex: none;
  }
  .contacts__text { margin: 0; }
  .brand {
    position: absolute;
    z-index: 1;
    right: 78px;
    top: 548px;
    margin: 0;
    font-family: "Open Sans", sans-serif;
    font-size: 50px;
    font-weight: 400;
    letter-spacing: 0.5px;
    color: var(--brand-grey);
  }
  .band {
    position: absolute;
    z-index: 1;
    left: 0;
    bottom: 0;
    width: 1200px;
    height: 40px;
    background: var(--band);
  }
</style>
</head>
<body>
<main class="card">
  <div class="emblem" role="img" aria-label="Brand emblem area: a rising sun behind stepped temple outlines in pale grey and soft yellow"></div>

  <div class="person">
    <p class="person__name">FIRST NAME</p>
    <p class="person__role">Designation</p>
  </div>

  <ul class="contacts">
    <li class="contacts__item">
      <span class="contacts__icon"><svg viewBox="0 0 36 36"><circle cx="18" cy="18" r="15"/><path d="M14 10 q-3 8 2 16 l3 -2 -2 -4 2 -2 -1 -6 z"/></svg></span>
      <span class="contacts__rule"></span>
      <p class="contacts__text">0400 555 184</p>
    </li>
    <li class="contacts__item">
      <span class="contacts__icon"><svg viewBox="0 0 36 36"><rect x="4" y="8" width="28" height="20"/><path d="M4 8 l14 11 14 -11 M4 28 l10 -10 M32 28 l-10 -10"/></svg></span>
      <span class="contacts__rule"></span>
      <p class="contacts__text">firstname@halvorenarchitects.com.au</p>
    </li>
    <li class="contacts__item">
      <span class="contacts__icon"><svg viewBox="0 0 36 36"><circle cx="18" cy="18" r="14"/><ellipse cx="18" cy="18" rx="6" ry="14"/><path d="M4 18 h28 M7 11 h22 M7 25 h22"/></svg></span>
      <span class="contacts__rule"></span>
      <p class="contacts__text">www.halvorenarchitects.com.au</p>
    </li>
    <li class="contacts__item contacts__item--gap">
      <span class="contacts__icon"><svg viewBox="0 0 36 36"><path d="M4 26 v-10 a6 6 0 0 1 12 0 v10 z M10 10 h18 a6 6 0 0 1 6 6 v10 h-18"/><path d="M22 16 h6 M26 16 v4"/></svg></span>
      <span class="contacts__rule"></span>
      <p class="contacts__text">1048 Lakeview WA 6921</p>
    </li>
    <li class="contacts__item contacts__item--tall">
      <span class="contacts__icon"><svg viewBox="0 0 36 36"><rect x="9" y="3" width="18" height="30"/><path d="M13 8 h3 M20 8 h3 M13 14 h3 M20 14 h3 M13 20 h3 M20 20 h3 M16 33 v-6 h4 v6"/></svg></span>
      <span class="contacts__rule"></span>
      <p class="contacts__text">Suite 9, 40 - 48 Harbourline<br>Drive, Lakeview, WA 6021</p>
    </li>
  </ul>

  <p class="brand">HALVOREN ARCHITECTS</p>

  <div class="band"></div>
</main>
</body>
</html>
```